Business Card Design for Property Development Company Director

I am looking for a professional and unforgettable business card design for our Director of our Property Development Company.
Please see attached .pptx file to find out what information to include. You don't have to follow the exact format shown in the file - I am interested to see your creative flair using the information provided.

```html
<!DOCTYPE html>
<html lang="en">
<head>
<meta charset="utf-8">
<title>Halvern Property Group – Business Card</title>
<link href="https://fonts.googleapis.com/css2?family=Montserrat:wght@400;500;600;700&display=swap" rel="stylesheet">
<style>
  :root {
    --bg: #e9eaec;
    --card: #f7f7f7;
    --blue: #1f5fb4;
    --grey: #555a60;
    --grey-light: #6d7278;
    --white: #ffffff;
  }
  * { margin: 0; padding: 0; box-sizing: border-box; }
  html, body { width: 1200px; height: 800px; overflow: hidden; }
  body {
    background: var(--bg);
    font-family: "Montserrat", sans-serif;
    display: flex;
    align-items: center;
    justify-content: center;
    gap: 50px;
  }
  .card {
    position: relative;
    width: 525px;
    height: 300px;
    background: var(--card);
    box-shadow: 0 6px 18px rgba(0,0,0,0.12);
    overflow: hidden;
  }

  /* Wordmark */
  .wordmark { display: flex; align-items: center; gap: 10px; }
  .wordmark-square { width: 30px; height: 30px; background: var(--blue); }
  .wordmark-text {
    color: var(--blue);
    font-weight: 700;
    font-size: 22px;
    line-height: 1.05;
    letter-spacing: 0.5px;
    text-transform: uppercase;
  }

  /* Front */
  .front-name {
    position: absolute; left: 32px; top: 34px;
    color: var(--blue); font-weight: 700; font-size: 19px;
    text-transform: uppercase;
  }
  .front-role {
    position: absolute; left: 32px; top: 58px;
    color: var(--grey-light); font-size: 12px;
  }
  .front-rule {
    position: absolute; left: 32px; top: 80px;
    width: 400px; height: 1px; background: var(--blue);
  }
  .contact-list {
    position: absolute; left: 32px; top: 96px;
    list-style: none; color: var(--grey); font-size: 12px;
  }
  .contact-list li { display: flex; align-items: center; gap: 7px; margin-bottom: 4px; }
  .contact-list svg { width: 9px; height: 9px; fill: none; stroke: var(--blue); stroke-width: 2; }
  .contact-list .accent { color: var(--blue); font-weight: 600; }
  .front .wordmark { position: absolute; right: 40px; top: 118px; }
  .front-address {
    position: absolute; right: 32px; top: 222px;
    text-align: right; color: var(--grey); font-size: 12.5px; line-height: 1.35;
  }
  .licence-band {
    position: absolute; right: 0; bottom: 0;
    width: 250px; height: 26px; background: var(--blue);
    color: var(--white); font-size: 11px;
    display: flex; align-items: center; padding-left: 18px;
  }

  /* Back */
  .back-tagline {
    position: absolute; right: 50px; top: 42px;
    text-align: right; color: var(--grey-light); font-size: 13px; line-height: 1.4;
  }
  .back .wordmark { position: absolute; left: 180px; top: 122px; }
  .back-prompt {
    position: absolute; left: 32px; bottom: 34px;
    color: var(--grey); font-size: 12.5px; font-weight: 500;
  }
  .back-prompt strong { color: var(--blue); font-weight: 600; }
</style>
</head>
<body>

  <section class="card front" aria-label="Business card front">
    <h1 class="front-name">Daniel Marsh</h1>
    <p class="front-role">Director</p>
    <div class="front-rule"></div>
    <ul class="contact-list">
      <li>
        <svg viewBox="0 0 10 10"><path d="M2 1 L4 3 L3 4 Q4.5 6 6 7 L7 6 L9 8 L7.5 9.3 Q3 8 0.8 2.5 Z"/></svg>
        0400 318 275
      </li>
      <li>
        <svg viewBox="0 0 10 10"><rect x="1" y="2" width="8" height="6"/><path d="M1 2 L5 5.5 L9 2"/></svg>
        daniel@halvern.com.au
      </li>
      <li>
        <svg viewBox="0 0 10 10"><circle cx="5" cy="5" r="4"/><path d="M1 5 H9 M5 1 Q2.5 5 5 9 M5 1 Q7.5 5 5 9"/></svg>
        <span>www.<span class="accent">halvern</span>.com.au</span>
      </li>
    </ul>
    <div class="wordmark">
      <span class="wordmark-square"></span>
      <span class="wordmark-text">Halvern<br>Property Group</span>
    </div>
    <address class="front-address" style="font-style:normal">
      42 Ashford St.<br>Northcote VIC 3070, Australia
    </address>
    <div class="licence-band">Real Estate Lic. 5102846 &amp; 5102847</div>
  </section>

  <section class="card back" aria-label="Business card back">
    <p class="back-tagline">Property Development<br>&amp; Site Acquisition Specialists</p>
    <div class="wordmark">
      <span class="wordmark-square"></span>
      <span class="wordmark-text">Halvern<br>Property Group</span>
    </div>
    <p class="back-prompt">Ask me about our <strong>INVESTMENT &amp; PARTNERSHIP</strong> opportunities</p>
  </section>

</body>
</html>
```